Business Card for a mobile physiotherapy company

I need a layout for a business card for a mobile physiotherapy company.
Slogan is "Mobile Physiotherapy - Your Road To Recovery"
Phone number is 867-555-0142
Email VardenTherapy@postnest.ca (subject to change with website)
Website www.VardenTherapy.ca
My name and credentials: Luke Varden Luke Varden, BSc(kin), MPT, CAFCI, IMS
Information maybe included: Direct Billing, Services including Physiotherapy, IMS, acupuncture
Maybe include facebook and instagram logos
One side with the logo clean and sharp
Other side with details, try not to look too busy, keep everything concise

```html
<!DOCTYPE html>
<html lang="en">
<head>
<meta charset="utf-8">
<title>Varden Therapy – Business Card</title>
<link rel="stylesheet" href="https://fonts.googleapis.com/css2?family=Montserrat:wght@400;500;600;700&display=swap">
<style>
  :root {
    --bg: #e6e8e8;
    --card: #ffffff;
    --card-shade: #eef0ef;
    --green: #0d5a4c;
    --green-dark: #0a4a3e;
    --navy: #23427a;
    --text-light: #eaf3f0;
    --sans: "Montserrat", Arial, sans-serif;
  }
  * { box-sizing: border-box; margin: 0; padding: 0; }
  html, body { width: 1200px; height: 997px; overflow: hidden; }
  body { background: var(--bg); font-family: var(--sans); position: relative; }

  .card {
    position: absolute; width: 700px; height: 400px;
    border-radius: 22px; overflow: hidden;
    background: linear-gradient(180deg, var(--card) 0%, var(--card-shade) 100%);
    box-shadow: 0 10px 30px rgba(0,0,0,.18);
  }
  .card--front { left: 80px; top: 70px; }
  .card--back { left: 420px; top: 520px; }

  /* Wordmark */
  .wordmark { display: flex; align-items: center; gap: 14px; color: var(--navy); font-weight: 700; letter-spacing: 3px; line-height: 1; }
  .wordmark__mark { width: 16px; height: 16px; background: var(--navy); flex: none; }
  .wordmark__name { font-size: 44px; text-transform: uppercase; }
  .wordmark__name small { display: block; font-size: 22px; letter-spacing: 12px; margin-top: 8px; font-weight: 700; }

  /* Front */
  .front__logo { position: absolute; left: 0; right: 0; top: 95px; display: flex; justify-content: center; }
  .front__tagline {
    position: absolute; left: 0; right: 0; top: 262px; text-align: center;
    color: var(--green); font-size: 14px; font-weight: 600; letter-spacing: 1px;
  }
  .front__band { position: absolute; left: 0; right: 0; bottom: 0; height: 72px; background: var(--green); }
  .front__rule { position: absolute; left: 0; right: 0; bottom: 78px; height: 3px; background: var(--navy); }
  .front__notch { position: absolute; left: 340px; bottom: 66px; }
  .front__services {
    position: absolute; left: 0; right: 0; bottom: 0; height: 72px;
    display: flex; align-items: center; justify-content: center;
    color: var(--text-light); font-size: 15px; font-weight: 500; letter-spacing: 1.5px;
  }

  /* Back */
  .back__panel { position: absolute; top: 0; bottom: 0; right: 0; width: 345px; background: var(--green); }
  .back__rule { position: absolute; top: 0; bottom: 0; right: 352px; width: 4px; background: var(--navy); }
  .back__notch { position: absolute; right: 331px; top: 100px; }
  .back__logo { position: absolute; left: 40px; top: 135px; }
  .back__social {
    position: absolute; left: 32px; width: 300px; bottom: 56px;
    display: flex; justify-content: space-between;
    color: var(--navy); font-size: 14px; font-weight: 700; white-space: nowrap;
  }
  .back__social span { display: flex; align-items: center; gap: 7px; }
  .back__social i { width: 9px; height: 9px; border-radius: 50%; background: var(--navy); display: inline-block; }

  .contact { position: absolute; left: 385px; top: 92px; color: var(--text-light); }
  .contact__name { font-size: 17px; font-weight: 700; letter-spacing: .5px; text-transform: uppercase; color: #fff; }
  .contact__creds { font-size: 13px; margin-top: 4px; }
  .contact__list { list-style: none; margin-top: 48px; }
  .contact__list li { display: flex; align-items: center; gap: 14px; font-size: 14px; height: 38px; }
  .contact__list li.web { font-weight: 700; color: #fff; }
  .contact__icon { width: 20px; height: 20px; flex: none; }
</style>
</head>
<body>

  <section class="card card--front" aria-label="Card front">
    <div class="front__logo">
      <div class="wordmark">
        <span class="wordmark__mark"></span>
        <span class="wordmark__name">Varden<small>Therapy</small></span>
      </div>
    </div>
    <p class="front__tagline">MOBILE PHYSIOTHERAPY - YOUR ROAD TO RECOVERY</p>
    <div class="front__rule"></div>
    <div class="front__band"></div>
    <svg class="front__notch" width="20" height="16" viewBox="0 0 20 16"><path d="M0 0 L10 12 L20 0" fill="var(--card-shade)" stroke="var(--navy)" stroke-width="3"/></svg>
    <p class="front__services">WE OFFER: DIRECT BILLING, PHYSIOTHERAPY, IMS, ACUPUNCTURE</p>
  </section>

  <section class="card card--back" aria-label="Card back">
    <div class="back__logo">
      <div class="wordmark">
        <span class="wordmark__mark"></span>
        <span class="wordmark__name">Varden<small>Therapy</small></span>
      </div>
    </div>
    <div class="back__social">
      <span><i></i>/VardenTherapy</span>
      <span><i></i>/VardenTherapy</span>
    </div>

    <div class="back__panel"></div>
    <div class="back__rule"></div>
    <svg class="back__notch" width="26" height="26" viewBox="0 0 26 26"><path d="M24 0 L10 13 L24 26" fill="var(--green)" stroke="var(--navy)" stroke-width="4"/></svg>

    <div class="contact">
      <p class="contact__name">Luke Varden</p>
      <p class="contact__creds">BSc(kin), MPT, CAFCI, IMS</p>
      <ul class="contact__list">
        <li>
          <svg class="contact__icon" viewBox="0 0 20 20"><rect width="20" height="20" rx="4" fill="#fff"/><path d="M6 5 L8 5 L9 8 L7.5 9 Q9 12 11 12.5 L12 11 L15 12 L15 14 Q10 15 7 11 Q5 8 6 5Z" fill="var(--green)"/></svg>
          867-555-0142
        </li>
        <li>
          <svg class="contact__icon" viewBox="0 0 20 20"><rect width="20" height="20" rx="4" fill="#fff"/><rect x="4" y="6" width="12" height="8" fill="none" stroke="var(--green)" stroke-width="1.5"/><path d="M4 6 L10 11 L16 6" fill="none" stroke="var(--green)" stroke-width="1.5"/></svg>
          VardenTherapy@postnest.ca
        </li>
        <li class="web">
          <svg class="contact__icon" viewBox="0 0 20 20"><rect width="20" height="20" rx="4" fill="#fff"/><rect x="4" y="5" width="12" height="8" rx="1" fill="none" stroke="var(--green)" stroke-width="1.5"/><path d="M8 16 H12 M10 13 V16" stroke="var(--green)" stroke-width="1.5"/></svg>
          www.VardenTherapy.ca
        </li>
      </ul>
    </div>
  </section>

</body>
</html>
```